Banner for promote service of debit card

We are PagoLume and we need the banners to be posted on the facebook and instagram pages.
We want something to communicate that it is an exclusive debit card full of services.
Low commissions.
Our competitors:
https://www.kelmora.example/it/home.html
https://www.zofe.example/it/
https://www.socialpage.example/ostrevabank/
monadrift
maybe some banner that makes the idea of a convenient debit card that everyone can use.
Girls enjoying card shopping.
Please check also website for slogans and phrases to use
https://www.pagolume.example/
Should show the services.
We must convey that it is a fast, simple card that guarantees privacy.
We need strong banners that attract people as these ban will be sponsored on instagram and facebook
People 18-35 y
Open Bank account. low commissions. Easy to use. No limits. 100% Privacy.
- Written in Italian.

```html
<!DOCTYPE html>
<html lang="it">
<head>
<meta charset="UTF-8">
<title>PagoLume – Una carta per tutti</title>
<link rel="stylesheet" href="https://fonts.googleapis.com/css2?family=Open+Sans:wght@400;600;700&family=Montserrat:wght@700&display=swap">
<style>
  :root {
    --sky: #bcdfe9;
    --sky-deep: #9fcfdd;
    --charcoal: #222528;
    --graphite: #3a3e42;
    --steel: #6d7377;
    --silver: #9aa0a3;
    --white: #ffffff;
    --ink: #111111;
    --brand-grey: #a3a6a8;
    --brand-accent: #f0503c;
    --fuchsia: #f0307a;
    --blush: #e9a6a0;
  }
  * { margin: 0; padding: 0; box-sizing: border-box; }
  html, body { width: 1200px; height: 1200px; overflow: hidden; }
  body { font-family: "Open Sans", Arial, sans-serif; background: var(--sky); }

  .banner { position: relative; width: 1200px; height: 1200px; overflow: hidden; }
  .backdrop { position: absolute; inset: 0; }

  .photo-area {
    position: absolute;
    left: 560px; top: 120px; width: 640px; height: 1080px;
    border-radius: 320px 320px 0 0;
    background:
      radial-gradient(ellipse at 40% 20%, rgba(196,140,90,.85) 0 22%, transparent 40%),
      radial-gradient(ellipse at 62% 58%, var(--fuchsia) 0 35%, transparent 62%),
      linear-gradient(180deg, rgba(233,166,160,.3), rgba(240,48,122,.55) 55%, rgba(235,235,235,.85));
  }

  .brand {
    position: absolute; left: 82px; top: 68px;
    display: flex; flex-direction: column; align-items: center; gap: 14px;
  }
  .brand-dot { width: 64px; height: 64px; border-radius: 50%; background: var(--brand-accent); }
  .brand-name { font-size: 40px; font-weight: 700; color: var(--brand-grey); letter-spacing: .2px; }

  .copy { position: absolute; left: 80px; color: var(--white); }
  .headline { top: 282px; font-size: 45px; font-weight: 700; line-height: 1.37; text-transform: uppercase; }
  .tagline { top: 474px; font-size: 41px; font-weight: 600; }
  .features { top: 556px; list-style: none; font-size: 23px; line-height: 37.5px; }

  .cta {
    position: absolute; left: 82px; top: 890px; width: 452px; height: 72px;
    border-radius: 36px; background: var(--white);
    display: flex; align-items: center; justify-content: center;
    font-family: "Montserrat", Arial, sans-serif; font-weight: 700; font-size: 22px;
    color: var(--ink); text-decoration: none;
  }
  .stripes { position: absolute; }
  .stripes-top { right: 24px; top: 36px; }
  .stripes-bottom { left: 0; bottom: 70px; }
</style>
</head>
<body>
<main class="banner">
  <svg class="backdrop" width="1200" height="1200" viewBox="0 0 1200 1200" aria-hidden="true">
    <defs>
      <linearGradient id="darkPanel" x1="0" y1="0" x2="1" y2="1">
        <stop offset="0" stop-color="#4a4e52"/>
        <stop offset=".5" stop-color="#2c2f33"/>
        <stop offset="1" stop-color="#1e2124"/>
      </linearGradient>
      <linearGradient id="greyBand" x1="0" y1="0" x2="1" y2="0">
        <stop offset="0" stop-color="#8d9397"/>
        <stop offset="1" stop-color="#5c6266"/>
      </linearGradient>
    </defs>
    <rect width="1200" height="1200" fill="#bcdfe9"/>
    <polygon points="0,0 760,0 0,760" fill="url(#greyBand)" opacity=".9"/>
    <polygon points="0,0 640,0 0,640" fill="#3b3f43"/>
    <polygon points="0,470 640,0 760,0 560,1200 0,1200" fill="url(#darkPanel)"/>
    <polygon points="0,560 0,700 560,150 520,100" fill="#9aa0a3" opacity=".55"/>
    <polygon points="420,1200 700,860 760,900 520,1200" fill="#6d7377" opacity=".6"/>
    <polygon points="300,1200 620,820 660,850 360,1200" fill="#9aa0a3" opacity=".35"/>
  </svg>

  <div class="photo-area" role="img" aria-label="Ragazza sorridente in abito fucsia con occhiali da sole bianchi, tiene una carta di pagamento e sacchetti della spesa"></div>

  <div class="brand">
    <span class="brand-dot" aria-hidden="true"></span>
    <span class="brand-name">PagoLume</span>
  </div>

  <h1 class="copy headline">All in one!<br>Una carta per tutti!</h1>
  <p class="copy tagline">Enjoy your card!</p>
  <ul class="copy features">
    <li>Fai quello che vuoi.</li>
    <li>Nessun limite.</li>
    <li>Nessun controllo</li>
    <li>Privacy garantita</li>
    <li>Usala come vuoi</li>
    <li>Senza essere controllato</li>
  </ul>

  <a class="cta" href="https://www.pagolume.example/">Otteni la tua Carta</a>

  <svg class="stripes stripes-top" width="150" height="64" viewBox="0 0 150 64" aria-hidden="true">
    <g stroke="#ffffff" stroke-width="7">
      <line x1="4" y1="62" x2="52" y2="2"/><line x1="28" y1="62" x2="76" y2="2"/>
      <line x1="52" y1="62" x2="100" y2="2"/><line x1="76" y1="62" x2="124" y2="2"/>
      <line x1="100" y1="62" x2="148" y2="2"/>
    </g>
  </svg>
  <svg class="stripes stripes-bottom" width="130" height="62" viewBox="0 0 130 62" aria-hidden="true">
    <g stroke="#ffffff" stroke-width="7">
      <line x1="-14" y1="60" x2="32" y2="2"/><line x1="10" y1="60" x2="56" y2="2"/>
      <line x1="34" y1="60" x2="80" y2="2"/><line x1="58" y1="60" x2="104" y2="2"/>
      <line x1="82" y1="60" x2="128" y2="2"/>
    </g>
  </svg>
</main>
</body>
</html>
```